Mobile App UI for Telecommunications/Hosting Company

We are about to convert our existing self-service Customer Portal into a mobile phone application and need an elegant and professional UI/UX design. Our company provides telecommunication (voice/mobile/data) and hosting services to medium-sized business. The primary purpose of the application is to view trouble tickets, alerts, orders, and performance charts. This application is available to customers only - not the general public.

Please provide a UI design suitable for display on iPhone/Android devices. The attached document includes a proposed screen flow. You are free to design your own screens to display the same information elegantly.
Updates

Please note that the design should be based on the wireframes in the Word document, not the screenshots.  The screenshots are just to show our existing web portal look & feel.

Also, just a few screens are required for initial submission (3 would be great).

Thanks,
Dermot.

Target Market(s)

IT Managers away from their desk and using a mobile phone application.
Adult males from technical background aged 30-50.
Customers of Brindlewood Telecom have access to this application (not the general public). This is a self-service portal for customers only.

Industry/Entity Type

Business

Colors
0592cd
33a6d7
85cae6
cadf82
fde08a

Requirements
Must have
• Please look at the screenshots from our current Customer Portal site (part of the project brief). The mobile app does not have to look the same, but should follow a similar style.

Please check out our company web site at www.brindlewoodtelecom.example (this site is not the customer portal and has a different look at feel) to understand what Brindlewood Telecom does.
Nice to have
• Sharing capabilities via email/SMS.
A nice background image to make it stand out
The colours selected below are a guide only as they are similar to the corporate colours
- The priority is something that works on a phone - a design extendable to tablets is a nice to have as our existing web site looks OK on a tablet..

```html
<!DOCTYPE html>
<html lang="en">
<head>
<meta charset="utf-8">
<title>Brindlewood Telecom – Navigation Drawer</title>
<link rel="stylesheet" href="https://fonts.googleapis.com/css2?family=Open+Sans:wght@400;600;700&display=swap">
<style>
  :root {
    --drawer-bg: #323232;
    --drawer-active: #5b5b5b;
    --divider: #474747;
    --text-light: #ffffff;
    --badge-grey: #5e5e5e;
    --badge-alert: #e2405f;
    --screen-text: #d6d2d0;
    --screen-alert: #e8445f;
    --screen-line: rgba(255,255,255,0.18);
  }
  * { box-sizing: border-box; margin: 0; padding: 0; }
  html, body { width: 676px; height: 1200px; overflow: hidden; background: #2a2a2a; }
  body { font-family: "Open Sans", sans-serif; color: var(--text-light); }

  .app { position: relative; width: 676px; height: 1200px; overflow: hidden; }

  /* Underlying screen */
  .screen {
    position: absolute; inset: 0;
    background: linear-gradient(170deg, #8a7d78 0%, #6f6663 30%, #5d5754 60%, #4b4746 100%);
  }
  .screen-header {
    position: absolute; left: 0; top: 0; width: 676px; height: 106px;
    background: rgba(190,185,182,0.55);
  }
  .screen-user { position: absolute; left: 588px; top: 27px; width: 52px; height: 52px; }
  .screen-count {
    position: absolute; left: 452px; top: 178px;
    font-size: 130px; font-weight: 700; line-height: 1; color: var(--text-light);
  }
  .screen-row {
    position: absolute; left: 0; width: 676px; height: 126px;
    border-bottom: 2px solid var(--screen-line);
    display: flex; align-items: center;
  }
  .screen-row span { position: absolute; left: 500px; font-size: 34px; color: var(--screen-text); }
  .screen-row.is-urgent span { color: var(--screen-alert); }

  /* Drawer */
  .drawer {
    position: absolute; left: 0; top: 0; width: 534px; height: 1200px;
    background: var(--drawer-bg); z-index: 2;
  }
  .drawer-profile {
    position: relative; height: 298px;
    background: linear-gradient(160deg, #6e6461 0%, #5a5250 45%, #4a4443 100%);
  }
  .drawer-close { position: absolute; left: 466px; top: 29px; width: 36px; height: 36px; }
  .avatar {
    position: absolute; left: 174px; top: 30px; width: 194px; height: 194px;
    border-radius: 50%; border: 6px solid #fff;
    background: radial-gradient(circle at 50% 40%, #b8a89c 0%, #8c7a70 60%, #6e625c 100%);
  }
  .profile-name {
    position: absolute; left: 0; width: 100%; top: 240px;
    text-align: center; font-size: 30px; color: var(--text-light);
  }

  .menu { list-style: none; }
  .menu-item {
    position: relative; height: 125px; display: flex; align-items: center;
    border-bottom: 2px solid var(--divider);
  }
  .menu-item.is-active { background: var(--drawer-active); border-bottom-color: var(--drawer-active); }
  .menu-icon { position: absolute; left: 21px; width: 56px; height: 56px; }
  .menu-label { position: absolute; left: 110px; font-size: 34px; letter-spacing: 0.5px; }
  .badge {
    position: absolute; left: 429px; width: 78px; height: 46px; border-radius: 23px;
    background: var(--badge-grey); font-size: 30px; line-height: 46px; text-align: center;
  }
  .badge.is-alert { background: var(--badge-alert); }

  .support-line { position: absolute; left: 17px; top: 1105px; font-size: 28px; }
</style>
</head>
<body>
<div class="app">
  <div class="screen" role="img" aria-label="Blurred background photograph behind the alerts screen">
    <div class="screen-header">
      <svg class="screen-user" viewBox="0 0 52 52" fill="none" stroke="#fff" stroke-width="3">
        <circle cx="26" cy="17" r="11"/>
        <path d="M4 49c2-12 11-18 22-18s20 6 22 18z"/>
      </svg>
    </div>
    <div class="screen-count">24</div>
    <div class="screen-row" style="top:360px"><span>Warning</span></div>
    <div class="screen-row is-urgent" style="top:488px"><span>Warning</span></div>
    <div class="screen-row" style="top:616px"><span>Warning</span></div>
    <div class="screen-row" style="top:744px"><span>Warning</span></div>
    <div class="screen-row" style="top:870px"><span>Warning</span></div>
    <div class="screen-row" style="top:996px"><span>Warning</span></div>
  </div>

  <nav class="drawer">
    <div class="drawer-profile" role="img" aria-label="Blurred profile background photograph">
      <svg class="drawer-close" viewBox="0 0 36 36" stroke="#fff" stroke-width="6" stroke-linecap="round">
        <path d="M5 5l26 26M31 5L5 31"/>
      </svg>
      <div class="avatar" role="img" aria-label="Profile photo of the signed-in user"></div>
      <div class="profile-name">User Rowan</div>
    </div>

    <ul class="menu">
      <li class="menu-item">
        <svg class="menu-icon" viewBox="0 0 56 56" fill="none" stroke="#fff" stroke-width="3" stroke-linejoin="round">
          <rect x="4" y="13" width="48" height="32" rx="3"/>
          <path d="M4 15l24 18 24-18"/>
        </svg>
        <span class="menu-label">ALERTS</span>
        <span class="badge">24</span>
      </li>
      <li class="menu-item is-active">
        <svg class="menu-icon" viewBox="0 0 56 56" fill="none" stroke="#fff" stroke-width="3" stroke-linejoin="round">
          <path d="M4 27L52 6 40 50 26 34z"/>
          <path d="M52 6L26 34v14l6-9"/>
        </svg>
        <span class="menu-label">ORDERS</span>
        <span class="badge is-alert">3</span>
      </li>
      <li class="menu-item">
        <svg class="menu-icon" viewBox="0 0 56 56" fill="none" stroke="#fff" stroke-width="3">
          <rect x="6" y="10" width="44" height="40" rx="3"/>
          <path d="M16 5v10M40 5v10M6 20h44"/>
          <g fill="#fff" stroke="none">
            <rect x="13" y="26" width="5" height="5"/><rect x="22" y="26" width="5" height="5"/><rect x="31" y="26" width="5" height="5"/><rect x="40" y="26" width="5" height="5"/>
            <rect x="13" y="36" width="5" height="5"/><rect x="22" y="36" width="5" height="5"/><rect x="31" y="36" width="5" height="5"/><rect x="40" y="36" width="5" height="5"/>
          </g>
        </svg>
        <span class="menu-label">TICKETS</span>
        <span class="badge">5</span>
      </li>
      <li class="menu-item">
        <svg class="menu-icon" viewBox="0 0 56 56" fill="none" stroke="#fff" stroke-width="3" stroke-linejoin="round" stroke-linecap="round">
          <path d="M3 38l12-12 10 8 12-12 16 12"/>
        </svg>
        <span class="menu-label">CHARTS</span>
      </li>
      <li class="menu-item">
        <svg class="menu-icon" viewBox="0 0 56 56" fill="none" stroke="#fff" stroke-width="3" stroke-linecap="round">
          <circle cx="28" cy="28" r="22"/>
          <path d="M28 17v22M17 28h22"/>
        </svg>
        <span class="menu-label">ADDRESS</span>
      </li>
      <li class="menu-item">
        <svg class="menu-icon" viewBox="0 0 56 56" fill="none" stroke="#fff" stroke-width="3" stroke-linejoin="round">
          <path d="M24 4h8l1.5 7 5 2.5 6-4 6 6-4 6 2 5 7 1.5v8l-7 1.5-2 5 4 6-6 6-6-4-5 2L32 52h-8l-1.5-7-5-2-6 4-6-6 4-6-2-5L1 32v-8l6.5-1.5 2-5-4-6 6-6 6 4 5-2.5z" transform="translate(0,0)"/>
          <circle cx="28" cy="28" r="9"/>
        </svg>
        <span class="menu-label">SETTINGS</span>
      </li>
    </ul>

    <p class="support-line">Support line:&nbsp; 555 - 0142 -0187</p>
  </nav>
</div>
</body>
</html>
```